Hello my Name is Elias Moreno. I buy and sell vintage comic books, you can refer to my instragram page qpkz.comics to get ideas and inspiration. For the front of the card I would like my company logo QPKZ Comics with a yellow and black background with the bat signal or bat emblem like on my IG page and with my info Elias Moreno as the Owner and address/ phone number, PO Box 617283, Miami, FL 33827, 305-482-6170 and that I buy and sell comics & collectables . Also feel free to be open to other ideas if you want. Im not stuck on one design. For the back of the card I would like for it to say follow me on Instagram QPKZ.Comics with the ig emblem. Also would like the card to be vertical if possible. Thanks

```html
<!DOCTYPE html>
<html lang="en">
<head>
<meta charset="utf-8">
<title>QPKZ Comics – Business Card</title>
<link rel="stylesheet" href="https://fonts.googleapis.com/css2?family=Source+Sans+3:wght@400;700&display=swap">
<style>
  :root {
    --backdrop: #3a322e;
    --card: #0b0b0b;
    --yellow: #f7c21a;
    --white: #ececec;
  }
  * { margin: 0; padding: 0; box-sizing: border-box; }
  html, body {
    width: 1200px; height: 844px; overflow: hidden;
    background: var(--backdrop);
    font-family: "Source Sans 3", sans-serif;
  }
  .stage {
    position: relative; width: 1200px; height: 844px;
    display: flex; align-items: center; justify-content: center; gap: 60px;
  }
  .card {
    position: relative;
    width: 520px; height: 300px;
    background: var(--card);
    box-shadow: 0 14px 30px rgba(0,0,0,.5);
  }
  .brand {
    position: absolute;
    display: flex; align-items: center; gap: 12px;
    color: var(--yellow); font-weight: 700; font-size: 34px;
    letter-spacing: .5px; white-space: nowrap;
  }
  .brand-dot {
    width: 30px; height: 30px; border-radius: 50%;
    background: var(--yellow);
  }
  .card-front .brand { left: 150px; top: 56px; }
  .contact {
    position: absolute; right: 30px; top: 132px;
    text-align: right; color: var(--white); font-size: 15px; line-height: 24px;
  }
  .contact .phone { display: inline-flex; align-items: center; gap: 6px; }
  .contact svg { width: 13px; height: 13px; fill: var(--yellow); }
  .tagline {
    color: var(--yellow); font-weight: 700; font-size: 18px; white-space: nowrap;
  }
  .card-front .tagline { position: absolute; right: 30px; top: 192px; }
  .owner { position: absolute; left: 30px; bottom: 36px; }
  .owner-name { color: var(--yellow); font-weight: 700; font-size: 20px; }
  .owner-role { color: var(--white); font-size: 14px; }
  .card-back {
    display: flex; flex-direction: column; align-items: center; justify-content: center;
  }
  .card-back .brand { position: static; margin-bottom: 40px; }
  .follow {
    display: flex; align-items: center; gap: 6px;
    color: var(--yellow); font-size: 16px; margin-bottom: 14px;
  }
  .follow-square {
    width: 16px; height: 16px; background: var(--white); border-radius: 3px;
  }
  .follow .handle { color: var(--white); }
</style>
</head>
<body>
<main class="stage">
  <section class="card card-front">
    <div class="brand"><span class="brand-dot"></span>QPKZ Comics</div>
    <div class="contact">
      <div class="phone">305-482-6170
        <svg viewBox="0 0 24 24" aria-hidden="true"><path d="M6.6 10.8a15.1 15.1 0 0 0 6.6 6.6l2.2-2.2a1 1 0 0 1 1-.25 11.4 11.4 0 0 0 3.6.57 1 1 0 0 1 1 1V20a1 1 0 0 1-1 1A17 17 0 0 1 3 4a1 1 0 0 1 1-1h3.5a1 1 0 0 1 1 1c0 1.25.2 2.45.57 3.57a1 1 0 0 1-.25 1z"/></svg>
      </div>
      <div class="address">PO Box 617283 Miami, FL 33827</div>
    </div>
    <p class="tagline">We buy and sell comics &amp; collectables</p>
    <div class="owner">
      <div class="owner-name">Elias Moreno</div>
      <div class="owner-role">Owner</div>
    </div>
  </section>

  <section class="card card-back">
    <div class="brand"><span class="brand-dot"></span>QPKZ Comics</div>
    <div class="follow">Follow me on <span class="follow-square"></span><span class="handle">QPKZ.Comics</span></div>
    <p class="tagline">We buy and sell comics &amp; collectables</p>
  </section>
</main>
</body>
</html>
```